Business Card Design Project

Business card based on attached logo

Todd Merrick
Todd@lorvantest.com
877-514-9073 ext. 318
Www.LorvanTest.com

Industry/Entity Type

Business

```html
<!DOCTYPE html>
<html lang="en">
<head>
<meta charset="utf-8">
<title>LorvanTest Business Cards</title>
<link href="https://fonts.googleapis.com/css2?family=Arimo:wght@400;700&display=swap" rel="stylesheet">
<style>
  :root {
    --stage: #8a8c8f;
    --ink: #231f20;
    --red: #e8262d;
    --red-dark: #c41f25;
    --red-soft: #ef3b3f;
    --paper: #f7f7f7;
    --paper-edge: #e4e4e4;
    --charcoal: #2b2b2b;
    --black: #111111;
    --white: #ffffff;
    --rule: #c9c9c9;
  }
  * { box-sizing: border-box; margin: 0; padding: 0; }
  html, body {
    width: 1200px; height: 720px; overflow: hidden;
    background: var(--stage);
    font-family: "Arimo", Arial, sans-serif;
  }
  .sheet { position: relative; width: 1200px; height: 720px; }
  .card {
    position: absolute; width: 564px; height: 321px;
    border-radius: 28px; overflow: hidden;
  }
  .card--front { left: 21px; top: 27px; background: linear-gradient(90deg, var(--paper-edge), var(--paper) 25%, var(--paper) 75%, var(--paper-edge)); border: 1px solid #6f6f6f; }
  .card--back { left: 609px; top: 27px; background: linear-gradient(90deg, var(--paper-edge), var(--paper) 25%, var(--paper) 75%, var(--paper-edge)); border: 1px solid #6f6f6f; }
  .card--dark { left: 21px; top: 373px; background: radial-gradient(ellipse at 50% 35%, #4a4a4a, var(--charcoal) 45%, var(--black)); }
  .card--red { left: 609px; top: 373px; background: linear-gradient(135deg, var(--red) 0%, var(--red-dark) 100%); }

  .brand {
    position: absolute; display: flex; align-items: center; gap: 12px;
    font-weight: 700; letter-spacing: -1px; line-height: 1;
  }
  .brand__mark { width: 18px; height: 18px; flex: none; }
  .card--front .brand { left: 0; right: 0; top: 62px; justify-content: center; font-size: 58px; color: var(--ink); }
  .card--front .brand__mark { background: var(--red); }
  .card--dark .brand { left: 0; right: 0; top: 110px; justify-content: center; font-size: 74px; color: var(--white); }
  .card--dark .brand__mark { background: var(--white); width: 22px; height: 22px; }
  .card--red .brand { left: 36px; top: 44px; font-size: 72px; color: var(--white); }

  .person { position: absolute; left: 0; right: 0; top: 213px; text-align: center; color: var(--red); font-size: 19px; }
  .divider { position: absolute; left: 38px; right: 50px; top: 243px; height: 2px; background: linear-gradient(90deg, transparent, var(--rule) 20%, var(--rule) 80%, transparent); }
  .contact { position: absolute; left: 0; right: 0; display: flex; justify-content: center; gap: 20px; color: var(--ink); font-size: 16.5px; }
  .contact--phone { top: 264px; }
  .contact--lines { top: 292px; }
  .contact__item { display: flex; align-items: center; gap: 7px; }
  .contact__icon { width: 13px; height: 13px; }

  .back-square { position: absolute; left: 184px; top: 52px; width: 198px; height: 198px; background: var(--red-soft); }
  .web { position: absolute; font-size: 16.5px; letter-spacing: 2.4px; }
  .card--back .web { left: 0; right: 0; top: 280px; text-align: center; color: var(--ink); }
  .card--dark .web { left: 0; right: 0; top: 297px; text-align: center; color: var(--white); }
  .card--red .web { left: 36px; top: 303px; color: var(--white); }

  .fade-square { position: absolute; left: 393px; top: 152px; width: 175px; height: 175px; background: rgba(255,255,255,0.13); }
</style>
</head>
<body>
<main class="sheet">

  <section class="card card--front">
    <div class="brand"><span>LorvanTest</span><span class="brand__mark"></span></div>
    <p class="person">TODD MERRICK</p>
    <div class="divider"></div>
    <div class="contact contact--phone">
      <span class="contact__item">
        <svg class="contact__icon" viewBox="0 0 16 16" aria-hidden="true"><path d="M3.5 1.5l2.5 0.5 1 3-1.8 1.3a9 9 0 0 0 4.5 4.5L11 9l3 1 .5 2.5-2 2C6.5 14 2 9.5 1.5 3.5z" fill="none" stroke="#231f20" stroke-width="1.4"/></svg>
        877-514-9073 ext. 318
      </span>
    </div>
    <div class="contact contact--lines">
      <span class="contact__item">
        <svg class="contact__icon" viewBox="0 0 16 16" aria-hidden="true"><rect x="1.5" y="3.5" width="13" height="9" fill="none" stroke="#231f20" stroke-width="1.4"/><path d="M1.5 4l6.5 5 6.5-5" fill="none" stroke="#231f20" stroke-width="1.4"/></svg>
        Todd@lorvantest.com
      </span>
      <span class="contact__item">
        <svg class="contact__icon" viewBox="0 0 16 16" aria-hidden="true"><circle cx="8" cy="8" r="6.5" fill="none" stroke="#231f20" stroke-width="1.3"/><ellipse cx="8" cy="8" rx="2.8" ry="6.5" fill="none" stroke="#231f20" stroke-width="1.1"/><path d="M1.5 8h13M2.5 5h11M2.5 11h11" stroke="#231f20" stroke-width="1"/></svg>
        www.lorvantest.com
      </span>
    </div>
  </section>

  <section class="card card--back">
    <div class="back-square"></div>
    <p class="web">www.lorvantest.com</p>
  </section>

  <section class="card card--dark">
    <div class="brand"><span>LorvanTest</span><span class="brand__mark"></span></div>
    <p class="web">www.lorvantest.com</p>
  </section>

  <section class="card card--red">
    <div class="brand"><span>LorvanTest</span></div>
    <div class="fade-square"></div>
    <p class="web">www.lorvantest.com</p>
  </section>

</main>
</body>
</html>
```